Kelvor Engineers: Why you should hire us keepsake

New design. Open to plastic cards. We are an engineering firm that designs cell phone towers and commercial buildings. Please check out our website www.kelvorstruct.com for more details. We want people to remember our card and for it to be useful if possible. We want the same look and feel on these cards to be translated to other marketing material we may need such as brochures.

Target Market(s)

Architects, Developers and Telecommunication Carriers

Industry/Entity Type

Engineering

Contact Information for Business Card

Card with our company colors, logo, and innovative design with elements related to our industry.

Font styles to use
Sans Serif

Colors
9bcb3c
abd036
0255a3

Requirements
Must have
• Sleek and hip design
Nice to have
• Bright lime green and navy coloring that pops with an innovative design.
Should not have
• A basic and boring design

```html
<!DOCTYPE html>
<html lang="en">
<head>
<meta charset="utf-8">
<title>Kelvor Engineers – Business Card</title>
<link href="https://fonts.googleapis.com/css2?family=Roboto:wght@400;700;900&family=Roboto+Condensed:wght@500;700&display=swap" rel="stylesheet">
<style>
  :root {
    --lime: #00f000;
    --navy: #022a5a;
    --paper: #f1f1f1;
    --white: #ffffff;
    --backdrop: #2b2b2b;
  }
  * { margin: 0; padding: 0; box-sizing: border-box; }
  html, body {
    width: 1200px; height: 960px; overflow: hidden;
    background: var(--backdrop);
    font-family: "Roboto", Arial, sans-serif;
  }
  .card {
    position: absolute;
    width: 600px; height: 343px;
    overflow: hidden;
    box-shadow: 0 2px 6px rgba(0,0,0,.5);
  }
  .card--front { left: 314px; top: 113px; background: var(--paper); }
  .card--back { left: 311px; top: 472px; background: var(--navy); }

  .front-shapes { position: absolute; inset: 0; }

  .contact {
    position: absolute; right: 38px; top: 40px;
    text-align: right; color: var(--white);
  }
  .contact__name {
    font-family: "Roboto Condensed", Arial, sans-serif;
    font-weight: 500; font-size: 22px; letter-spacing: .2px;
    margin-bottom: 13px;
  }
  .contact__line {
    display: flex; justify-content: flex-end; align-items: center;
    gap: 9px; font-size: 14.5px; line-height: 19px;
  }
  .contact__line svg { width: 13px; height: 13px; fill: var(--white); }

  .brand-front {
    position: absolute; left: 84px; top: 196px;
    font-weight: 900; font-size: 86px; letter-spacing: -2px;
    color: var(--navy);
  }

  .brand-back {
    position: absolute; left: 0; right: 0; top: 100px;
    text-align: center;
    font-weight: 900; font-size: 108px; letter-spacing: -3px;
    color: var(--lime);
  }
  .tagline {
    position: absolute; left: 0; right: 0; top: 266px;
    display: flex; justify-content: center; align-items: center; gap: 2px;
    font-weight: 700; font-size: 15px; color: var(--lime);
  }
  .tagline::before, .tagline::after {
    content: ""; width: 30px; height: 1.5px; background: var(--white);
  }
  .locations {
    position: absolute; left: 0; right: 0; top: 288px;
    text-align: center; font-size: 15px; letter-spacing: .4px;
    color: var(--white);
  }
</style>
</head>
<body>

<section class="card card--front">
  <svg class="front-shapes" viewBox="0 0 600 343" width="600" height="343" aria-hidden="true">
    <polygon points="206,0 600,0 600,343 512,343" fill="var(--lime)"/>
    <line x1="206" y1="0" x2="512" y2="343" stroke="var(--navy)" stroke-width="2.5"/>
    <polygon points="0,245 86,343 0,343" fill="var(--lime)"/>
    <line x1="0" y1="245" x2="86" y2="343" stroke="var(--navy)" stroke-width="2.5"/>
  </svg>

  <div class="brand-front">Kelvor</div>

  <div class="contact">
    <div class="contact__name">DANA HOLLIS MARDEN</div>
    <div class="contact__line">555.014.2290
      <svg viewBox="0 0 24 24"><path d="M6.6 10.8a15.1 15.1 0 0 0 6.6 6.6l2.2-2.2c.3-.3.7-.4 1-.2 1.1.4 2.3.6 3.6.6.6 0 1 .4 1 1V20c0 .6-.4 1-1 1A17 17 0 0 1 3 4c0-.6.4-1 1-1h3.5c.6 0 1 .4 1 1 0 1.3.2 2.5.6 3.6.1.3 0 .7-.2 1z"/></svg>
    </div>
    <div class="contact__line">555.017.4463
      <svg viewBox="0 0 24 24"><path d="M7 1h10a2 2 0 0 1 2 2v18a2 2 0 0 1-2 2H7a2 2 0 0 1-2-2V3a2 2 0 0 1 2-2zm0 3v14h10V4zm5 15.5a1.2 1.2 0 1 0 0 2.4 1.2 1.2 0 0 0 0-2.4z"/></svg>
    </div>
    <div class="contact__line">dmarden@kelvorstruct.com
      <svg viewBox="0 0 24 24"><path d="M2 5h20v14H2zm2 2v.5l8 5 8-5V7l-8 5z"/></svg>
    </div>
    <div class="contact__line">www.kelvorstruct.com
      <svg viewBox="0 0 24 24"><path d="M12 2a10 10 0 1 0 0 20 10 10 0 0 0 0-20zm-1 17.9A8 8 0 0 1 4.2 10.7L9 15.5v1a2 2 0 0 0 2 2zm6.9-2.5A2 2 0 0 0 16 16h-1v-3a1 1 0 0 0-1-1H8v-2h2a1 1 0 0 0 1-1V7h2a2 2 0 0 0 2-2v-.4a8 8 0 0 1 2.9 12.8z"/></svg>
    </div>
  </div>
</section>

<section class="card card--back">
  <div class="brand-back">Kelvor</div>
  <div class="tagline">MULTI-DISCIPLINE ENGINEERING</div>
  <div class="locations">Northgate | Riverton | Eastfield | Harbor Point</div>
</section>

</body>
</html>
```